Website Design for Cirrovane Cloud As a Service

We are building a service to allow customers to own their own private clouds easily and cheaply. Owning your own private cloud saves costs, and offers more flexibility than a public cloud provider but has historically been a complex and expensive option.

We plan to offer a service where we build and maintain your own private cloud on your own hardware for a cheap monthly costs. Similar to this service - https://nimbrovex.com/solutions/private-cloud

We already have a logo and branding in place - we'd like a website design to be tailored from this branding, see attached logo design.

Feel free to add important elements on the home page such as testimonials, client/partner logos, contact form, social media, etc using placeholder contents in addition to the document we attached.

We also plan to add sub-pages in the future so please make sure that your website design has a full navigation menu.

An example of the site we like: https://www.quorvant.com/ we'd be happy for you to take inspiration from this website.

Target Market(s)

B2B focused, we are targeting start-up/small/medium sized companies who needs help with their cloud and IT infrastructure.

Industry/Entity Type

IT

Number of Pages Required

1 page

Font styles to use
Other font styles liked:
• Please refer to the attachment - font must have Mayeka Demi Bold & Retroica

Requirements
Must have
• Please add placeholder menu since we're planning to have subpages later on.

```html
<!DOCTYPE html>
<html lang="en">
<head>
<meta charset="utf-8">
<title>Cirrovane Cloud as a Service</title>
<link rel="stylesheet" href="https://fonts.googleapis.com/css2?family=Comfortaa:wght@500;700&family=Quicksand:wght@500;600;700&display=swap">
<style>
:root{
  --blue:#2a8ad3;
  --blue-dark:#1f74b8;
  --ink:#2e2e33;
  --text:#3a3a40;
  --pale:#e3f0fb;
  --pale-2:#cfe4f6;
  --line:#bcd9f1;
  --footer:#2c2c2e;
  --white:#ffffff;
}
*{box-sizing:border-box;margin:0;padding:0}
html,body{width:1200px;height:4394px;overflow:hidden}
body{position:relative;font-family:"Quicksand",sans-serif;color:var(--text);background:var(--white)}
.abs{position:absolute}
h1,h2,h3,.display{font-family:"Comfortaa",sans-serif;font-weight:700}
.accent{color:var(--blue)}
.btn{position:absolute;display:flex;align-items:center;justify-content:center;background:var(--blue);color:var(--white);border-radius:30px;font-family:"Comfortaa",sans-serif;font-weight:700;font-size:23px}
.rule{position:absolute;height:4px;background:var(--blue)}

/* hero */
.hero{position:absolute;left:0;top:0;width:1200px;height:781px;background:linear-gradient(180deg,#f3f9fe 0%,#dcecfa 100%);overflow:hidden}
.brand{position:absolute;display:flex;align-items:center;gap:10px;font-family:"Comfortaa",sans-serif;font-weight:700;color:var(--blue)}
.brand .dot{width:36px;height:36px;border-radius:50%;background:var(--blue)}
.nav{position:absolute;left:518px;top:54px;display:flex;gap:34px;font-size:16px;font-weight:600;color:var(--ink)}
.login{position:absolute;left:1013px;top:43px;width:113px;height:44px;border-radius:22px;background:var(--blue);color:#fff;display:flex;align-items:center;justify-content:center;font-size:17px;font-weight:600}
.hero h1{position:absolute;left:74px;top:232px;width:560px;font-size:42px;line-height:48px;color:var(--blue);font-weight:700}
.hero .lead{position:absolute;left:74px;top:440px;width:540px;font-size:19.5px;line-height:28px;font-weight:700;color:var(--ink)}
.hero .sub{position:absolute;left:74px;top:540px;width:540px;font-size:19px;line-height:28px;font-weight:500;color:var(--ink)}
.hero-art{position:absolute;left:600px;top:150px;width:580px;height:560px;border-radius:40px;background:radial-gradient(ellipse at 60% 45%,#bcdaf4 0%,#d7eaf9 55%,rgba(220,236,250,0) 75%)}

/* benefits */
.section-title{position:absolute;left:0;width:1200px;text-align:center;font-family:"Comfortaa",sans-serif;font-weight:700;font-size:40px;line-height:48px;color:var(--ink)}
.benefit{position:absolute;width:330px}
.benefit h3{font-family:"Quicksand",sans-serif;font-size:19px;font-weight:600;color:var(--blue);line-height:22px;letter-spacing:.3px}
.benefit p{font-size:14px;line-height:20px;color:var(--ink);font-weight:500;margin-top:6px}
.benefit.left{text-align:right}
.ring-node{position:absolute;width:80px;height:80px;border-radius:50%;background:#fff;box-shadow:0 4px 14px rgba(42,138,211,.18);display:flex;align-items:center;justify-content:center}
.ring-node .core{width:48px;height:48px;border-radius:50%;display:flex;align-items:center;justify-content:center}
.ring-node.solid .core{background:var(--blue);width:80px;height:80px}

/* drive */
.drive{position:absolute;left:0;top:1488px;width:1200px;height:626px;background:linear-gradient(135deg,#e6f2fc 0%,#d4e8f8 100%);overflow:hidden}
.drive .copy{position:absolute;left:80px;top:210px;width:1040px;text-align:center;font-size:14.5px;line-height:28px;font-weight:500;color:var(--ink)}
.pill{position:absolute;top:392px;width:242px;height:60px;border:2px solid var(--line);border-radius:30px;display:flex;align-items:center;justify-content:center;gap:10px;font-size:22px;font-weight:600;color:var(--ink);background:rgba(255,255,255,.25)}

/* public cloud cards */
.card{position:absolute;top:2311px;width:328px;height:367px;border:2px solid #9fcbed;text-align:center;background:#fff}
.card .icon{position:absolute;left:108px;top:24px;width:112px;height:112px;border-radius:50%;background:var(--pale);display:flex;align-items:center;justify-content:center}
.card h3{position:absolute;left:16px;top:160px;width:296px;font-family:"Quicksand",sans-serif;font-size:19px;line-height:24px;font-weight:600;color:var(--blue)}
.card p{position:absolute;left:20px;width:288px;font-size:14px;line-height:25px;font-weight:500;color:var(--ink)}

/* difference */
.difference{position:absolute;left:0;top:2850px;width:1200px;height:721px;background:linear-gradient(180deg,#eaf4fd 0%,#d6e9f8 100%)}
.diff-art{position:absolute;left:9px;top:48px;width:572px;height:613px;border-radius:50% 50% 48% 52%/40% 40% 60% 60%;background:radial-gradient(ellipse at 50% 70%,#9ccbee 0%,#c4e0f6 45%,rgba(214,233,248,0) 72%)}
.diff-list{position:absolute;left:615px;top:180px;width:520px;list-style:none}
.diff-list li{position:relative;padding-left:34px;font-size:14.5px;line-height:25px;font-weight:500;color:var(--ink);margin-bottom:13px}
.diff-list li svg{position:absolute;left:0;top:5px}

/* contact */
.contact-row{position:absolute;left:74px;display:flex;align-items:center;gap:26px;font-size:21px;font-weight:600;color:var(--ink)}
.contact-row .ic{width:50px;height:50px;border-radius:50%;border:2px solid var(--line);display:flex;align-items:center;justify-content:center;background:#fff}
.field{position:absolute;height:50px;border:1.5px solid #c9c9cc;border-radius:25px;padding-left:24px;display:flex;align-items:center;font-size:15px;font-weight:600;color:var(--ink);background:#fff}

/* footer */
.footer{position:absolute;left:0;top:4077px;width:1200px;height:317px;background:var(--footer);color:#fff}
.fcol{position:absolute;top:64px}
.fcol h4{font-family:"Quicksand",sans-serif;font-size:21px;font-weight:600;color:var(--blue);letter-spacing:.5px;margin-bottom:6px}
.fcol a{display:block;color:#fff;text-decoration:none;font-size:15px;font-weight:500;line-height:35px}
.social{position:absolute;left:75px;top:4301px;display:flex;gap:18px}
.social span{width:24px;height:24px;border-radius:4px;background:#fff}
</style>
</head>
<body>

<header class="hero">
  <div class="brand" style="left:74px;top:40px;font-size:32px"><span class="dot"></span>Cirrovane Cloud</div>
  <nav class="nav"><span>Products</span><span>Solutions</span><span>Pricing</span><span>Resources</span><span>About</span></nav>
  <div class="login">Log In</div>
  <h1>A Groundbreaking Way For Your Small Business To Benefit From The Power Of The Cloud</h1>
  <p class="lead">Cirrovane Cloud as a Service is here to help small businesses utilise the power of the cloud without complicated set ups or scary price tags.</p>
  <p class="sub">Ready to modernise your infrastructure with a fully managed private cloud solution from CCaas?</p>
  <a class="btn" style="left:75px;top:626px;width:200px;height:58px">Contact Us</a>
  <div class="hero-art" role="img" aria-label="Illustration of a person working on a laptop at a desk beneath a cloud with files and documents uploading"></div>
</header>

<section aria-label="Benefits">
  <h2 class="section-title" style="top:846px">How <span class="accent">CCAAS</span> Benefits Your Business</h2>
  <div class="rule" style="left:525px;top:915px;width:150px"></div>

  <svg class="abs" style="left:390px;top:978px" width="420" height="420" viewBox="0 0 420 420">
    <circle cx="210" cy="210" r="200" fill="none" stroke="#9fcbed" stroke-width="1.5" stroke-dasharray="5 6"/>
    <circle cx="210" cy="210" r="170" fill="#eef6fd"/>
    <circle cx="210" cy="210" r="145" fill="#fff" stroke="#d7eaf9" stroke-width="6"/>
    <circle cx="210" cy="220" r="70" fill="var(--blue)"/>
  </svg>

  <div class="ring-node" style="left:430px;top:990px"><div class="core"><svg width="32" height="26" viewBox="0 0 32 26" fill="none" stroke="#2a8ad3" stroke-width="3"><path d="M2 4h28M2 13h28M2 22h28"/><circle cx="10" cy="4" r="3" fill="#fff"/><circle cx="22" cy="13" r="3" fill="#fff"/><circle cx="14" cy="22" r="3" fill="#fff"/></svg></div></div>
  <div class="ring-node solid" style="left:705px;top:990px"><div class="core"><span style="color:#fff;font-size:32px;font-weight:700">$</span></div></div>
  <div class="ring-node" style="left:360px;top:1146px"><div class="core" style="background:var(--blue);width:34px;height:34px"><svg width="18" height="18" viewBox="0 0 18 18" fill="none" stroke="#fff" stroke-width="2"><path d="M9 3v6l4 2"/></svg></div></div>
  <div class="ring-node" style="left:763px;top:1146px"><div class="core"><svg width="22" height="30" viewBox="0 0 22 30"><circle cx="11" cy="11" r="10" fill="#2a8ad3"/><rect x="7" y="21" width="8" height="6" rx="2" fill="#2a8ad3"/></svg></div></div>
  <div class="ring-node" style="left:430px;top:1303px"><div class="core"><svg width="30" height="30" viewBox="0 0 30 30" fill="#2a8ad3"><rect x="2" y="13" width="6" height="14" rx="1"/><path d="M10 13l6-11c3 0 4 2 3 5l-1 5h8c2 0 3 2 2 4l-3 9c-1 2-2 2-4 2H10z"/></svg></div></div>
  <div class="ring-node" style="left:705px;top:1303px"><div class="core"><svg width="32" height="26" viewBox="0 0 32 26" fill="none" stroke="#2a8ad3" stroke-width="3"><path d="M2 2v22h28"/><path d="M6 18l7-7 5 5 10-10"/></svg></div></div>

  <div class="benefit left" style="left:74px;top:988px"><h3>TOTALLY FLEXIBLE</h3><p>Get the cloud you want and the latest<br>innovations you need</p></div>
  <div class="benefit" style="left:808px;top:988px"><h3>NO CONSULTANCY FEES</h3><p>We’ll work with you and charge<br>set fees for everything</p></div>
  <div class="benefit left" style="left:8px;top:1152px"><h3>FASTER</h3><p>Our private cloud solutions<br>outpace public clouds</p></div>
  <div class="benefit" style="left:861px;top:1142px"><h3>TRIED AND TESTED CLOUD<br>SOLUTIONS</h3><p>We’ll deploy the right OpenStratum<br>solutions for your business</p></div>
  <div class="benefit left" style="left:74px;top:1318px"><h3>GREATER VALUE FOR MONEY</h3><p>Totally transparent pricing for no<br>nasty month-end surprises</p></div>
  <div class="benefit" style="left:803px;top:1318px"><h3>MANAGEMENT, MONITORING<br>AND MAINTENANCE</h3><p>They’re all included in your<br>monthly price</p></div>
</section>

<section class="drive" aria-label="Digital transformation">
  <svg class="abs" style="left:0;top:0" width="1200" height="626" viewBox="0 0 1200 626" fill="#c9e1f5" opacity=".55">
    <circle cx="640" cy="560" r="360"/>
  </svg>
  <h2 class="section-title" style="top:63px"><span class="accent">CCAAS</span> Can Drive Your Digital<br>Transformation Today</h2>
  <p class="copy">Organisations of all shapes and sizes are reaping the time and money saving benefits that the cloud brings. But for small businesses seeking to transition, managing the time and financial costs of transitioning, and knowing whether to opt for a public or private cloud can cause you to hit the pause button.<br>CCAAS is here to help you switch on your cloud transformation in a way that works best for you.&nbsp; We deliver and support fully managed private cloud solutions that are:</p>
  <div class="pill" style="left:77px"><svg width="20" height="16" viewBox="0 0 20 16" fill="none" stroke="#2e2e33" stroke-width="3.5"><path d="M2 8l6 6L18 2"/></svg>FAST</div>
  <div class="pill" style="left:348px"><svg width="20" height="16" viewBox="0 0 20 16" fill="none" stroke="#2e2e33" stroke-width="3.5"><path d="M2 8l6 6L18 2"/></svg>EASY</div>
  <div class="pill" style="left:617px"><svg width="20" height="16" viewBox="0 0 20 16" fill="none" stroke="#2e2e33" stroke-width="3.5"><path d="M2 8l6 6L18 2"/></svg>POWERFUL</div>
  <div class="pill" style="left:886px"><svg width="20" height="16" viewBox="0 0 20 16" fill="none" stroke="#2e2e33" stroke-width="3.5"><path d="M2 8l6 6L18 2"/></svg>SCALABLE</div>
  <a class="btn" style="left:500px;top:499px;width:200px;height:58px">Get Started</a>
</section>

<section aria-label="Public cloud">
  <h2 class="section-title" style="top:2171px">If You’re Using A Public Cloud Now</h2>
  <div class="rule" style="left:525px;top:2250px;width:150px"></div>

  <div class="card" style="left:75px">
    <div class="icon"><svg width="54" height="30" viewBox="0 0 54 30"><rect x="1" y="1" width="52" height="28" rx="3" fill="#2a8ad3"/><circle cx="27" cy="15" r="7" fill="#fff"/><circle cx="9" cy="15" r="3" fill="#fff"/><circle cx="45" cy="15" r="3" fill="#fff"/></svg></div>
    <h3>YOU COULD BE PAYING<br>TOO MUCH</h3>
    <p style="top:224px">Public cloud pricing structures have a habit of sneakily scaling up very quickly. With CCAAS, you’ll always know what you’re paying for your private cloud services.</p>
  </div>
  <div class="card" style="left:438px">
    <div class="icon"><svg width="30" height="40" viewBox="0 0 30 40"><path d="M2 2h18l8 8v28H2z" fill="#2a8ad3"/><path d="M8 20h14M8 26h14M8 32h14" stroke="#fff" stroke-width="2.5"/></svg></div>
    <h3>YOU’RE LIKELY NOT<br>GETTING THE BENEFITS OF<br>FULL FUNCTIONALITY</h3>
    <p style="top:248px">Public cloud providers cannot adopt new innovations and functions as quickly and easily as the private cloud solutions you’ll get from CCAAS.</p>
  </div>
  <div class="card" style="left:799px">
    <div class="icon"><svg width="58" height="38" viewBox="0 0 58 38" fill="#2a8ad3"><circle cx="20" cy="24" r="13"/><circle cx="33" cy="16" r="15"/><circle cx="46" cy="26" r="11"/><rect x="10" y="24" width="40" height="13" rx="6"/></svg></div>
    <h3>YOU’LL BE TIED TO THE<br>SERVICES YOUR PROVIDER<br>CAN PROVIDE</h3>
    <p style="top:248px">Public cloud providers will have a limited suite of products and services to offer you. A CCAAS private cloud has no such limitations</p>
  </div>
  <a class="btn" style="left:500px;top:2722px;width:200px;height:58px">Let’s Talk</a>
</section>

<section class="difference" aria-label="The CCAAS difference">
  <div class="diff-art" role="img" aria-label="Isometric illustration of two people at computer desks connected to a cloud holding a folder of files"></div>
  <h2 class="abs display" style="left:615px;top:72px;font-size:42px;color:var(--ink)">The <span class="accent">CCAAS</span> Difference</h2>
  <div class="rule" style="left:615px;top:142px;width:150px"></div>
  <ul class="diff-list">
    <li><svg width="16" height="16" viewBox="0 0 16 16"><circle cx="8" cy="8" r="8" fill="#2a8ad3"/><path d="M4 8l3 3 5-6" fill="none" stroke="#fff" stroke-width="2"/></svg>We’ll quickly get to grips with what your organisation needs, and deliver it via our private cloud solutions.</li>
    <li><svg width="16" height="16" viewBox="0 0 16 16"><circle cx="8" cy="8" r="8" fill="#2a8ad3"/><path d="M4 8l3 3 5-6" fill="none" stroke="#fff" stroke-width="2"/></svg>Enjoy the ease of the public cloud, combined with the features, innovations and flexibility of the private cloud.</li>
    <li><svg width="16" height="16" viewBox="0 0 16 16"><circle cx="8" cy="8" r="8" fill="#2a8ad3"/><path d="M4 8l3 3 5-6" fill="none" stroke="#fff" stroke-width="2"/></svg>You can focus on your core business while we support you with a dedicated cloud infrastructure.</li>
    <li><svg width="16" height="16" viewBox="0 0 16 16"><circle cx="8" cy="8" r="8" fill="#2a8ad3"/><path d="M4 8l3 3 5-6" fill="none" stroke="#fff" stroke-width="2"/></svg>We’ll create and deliver the launchpad that will take your business forward.</li>
    <li><svg width="16" height="16" viewBox="0 0 16 16"><circle cx="8" cy="8" r="8" fill="#2a8ad3"/><path d="M4 8l3 3 5-6" fill="none" stroke="#fff" stroke-width="2"/></svg>Get the benefits of your own cloud infrastructure and reduce your operational costs.</li>
    <li><svg width="16" height="16" viewBox="0 0 16 16"><circle cx="8" cy="8" r="8" fill="#2a8ad3"/><path d="M4 8l3 3 5-6" fill="none" stroke="#fff" stroke-width="2"/></svg>Fast and easy computing, storage and network resources.</li>
    <li><svg width="16" height="16" viewBox="0 0 16 16"><circle cx="8" cy="8" r="8" fill="#2a8ad3"/><path d="M4 8l3 3 5-6" fill="none" stroke="#fff" stroke-width="2"/></svg>Managed operations from private OpenStratum clouds and Kubelane.</li>
    <li><svg width="16" height="16" viewBox="0 0 16 16"><circle cx="8" cy="8" r="8" fill="#2a8ad3"/><path d="M4 8l3 3 5-6" fill="none" stroke="#fff" stroke-width="2"/></svg>We’ll support your growth and scale your cloud as you need it.</li>
  </ul>
</section>

<section aria-label="Contact">
  <svg class="abs" style="left:0;top:3571px" width="1200" height="506" viewBox="0 0 1200 506"><circle cx="420" cy="430" r="330" fill="#edf5fc"/></svg>
  <h2 class="abs display" style="left:74px;top:3636px;font-size:40px;color:var(--ink)">Contact <span class="accent">Us</span></h2>
  <div class="rule" style="left:74px;top:3708px;width:150px"></div>
  <h2 class="abs display" style="left:615px;top:3636px;font-size:40px;color:var(--ink)">Quick <span class="accent">Contact</span></h2>
  <div class="rule" style="left:615px;top:3708px;width:150px"></div>

  <div class="contact-row" style="top:3771px"><span class="ic"><svg width="18" height="24" viewBox="0 0 18 24"><path d="M9 1a8 8 0 0 1 8 8c0 6-8 14-8 14S1 15 1 9a8 8 0 0 1 8-8z" fill="#2e2e33"/><circle cx="9" cy="9" r="3" fill="#fff"/></svg></span><span style="line-height:28px">27 Larchfield Lane, Dunmore,<br>DN4 7QX</span></div>
  <div class="contact-row" style="top:3849px"><span class="ic"><svg width="20" height="22" viewBox="0 0 20 22" fill="none" stroke="#2e2e33" stroke-width="2.5"><path d="M5 2l3 5-2 3c1 3 3 5 6 6l3-2 4 3-2 4C9 21 1 13 1 5z"/></svg></span><span>1-555-0142-7700</span></div>
  <div class="contact-row" style="top:3930px"><span class="ic"><svg width="24" height="24" viewBox="0 0 24 24"><circle cx="12" cy="12" r="11" fill="#2e2e33"/><path d="M6 9l6 4 6-4v7H6z" fill="#fff"/></svg></span><span>hello@cirrovane.example</span></div>

  <div class="field" style="left:615px;top:3772px;width:430px">Name</div>
  <div class="field" style="left:615px;top:3834px;width:430px">Email Address</div>
  <div class="field" style="left:615px;top:3895px;width:212px">Phone</div>
  <div class="field" style="left:840px;top:3895px;width:205px">Subject</div>
  <a class="btn" style="left:615px;top:3956px;width:205px;height:51px;font-size:21px">Submit</a>
</section>

<footer class="footer">
  <div class="brand" style="left:74px;top:98px;font-size:32px;color:#fff"><span class="dot"></span>Cirrovane Cloud</div>
  <p class="abs" style="left:75px;top:164px;font-size:14px;line-height:24px;font-weight:500">Copyright © 2022 Company Name<br>All Rights Reserved</p>
  <div class="fcol" style="left:435px"><h4>COMPANY</h4><a>Sed ut perspiciatis</a><a>Unde omnis iste</a><a>Natus error</a><a>Sit voluptatem</a><a>Accusantium dolore</a></div>
  <div class="fcol" style="left:692px"><h4>PRODUCTS</h4><a>Sed ut perspiciatis</a><a>Unde omnis iste</a><a>Natus error</a><a>Sit voluptatem</a><a>Accusantium dolore</a></div>
  <div class="fcol" style="left:929px"><h4>RESOURCES</h4><a>Sed ut perspiciatis</a><a>Unde omnis iste</a><a>Natus error</a><a>Sit voluptatem</a><a>Accusantium dolore</a></div>
</footer>
<div class="social" aria-label="Social media links"><span></span><span></span><span></span><span></span><span></span></div>

</body>
</html>
```